Real estate Investment post card Design

I need a post card for Real Estate Marketing.

There are several similar cards on line.
Please see the post cards in this link to vidmarlo
https://www.vidmarlo.com/watch?v=pQ7tR2mZ9wL
At 1:18 the back of the card is very good.
For front of the card please refer to attached example gif.

Please also check the examples posted by me.

Everything needs to be the same except
1. Tovin Buys Houses
2. Phone number 347 815 9026
3. Website www.brelkaporch.com
4. Email info@brelkaporch.com
5. Picture needs to be replaced with my picture

The postcards need to be 2 sides and in color

Please let me know

Target Market(s)

Home owners who want to sell their houses for quick settlement and cash

Industry/Entity Type

Real Estate

Requirements
Must have
• I am copying this from another project as i think these instructions are valid for this project as well.
• Attention Designers - Special Requirements
• This project has special US Postcard Design requirements that apply to all submissions. The project is part of a print initiative, meaning that the selected design will be sent directly to print. If you have not, click download the templates below and ensure your design follows them before submitting.
• I plan to print the Post card by quellpress in their Jumbo Format... copied below
• Document Trim Size
• 8.52" x 5.47"
• 216 x 139 mm
• 2556 x 1642 pixels
• Full Bleed Size
• Horizontal
• 8.64" x 5.59"
• 219 x 142 mm
• 2592 x 1677 pixels
• NOTE Please make sure you put return address on the post card
• 2874 9TH ST., PO Box. 5617
• WEST ORLEN FALLS, NY 11592
Nice to have
• Please see if you can add pictures that signify cash $$ and houses in the project. See the attached vidmarlo.
Should not have
• Too much text on the first page

```html
<!DOCTYPE html>
<html lang="en">
<head>
<meta charset="utf-8">
<title>Tovin Buys Houses on Cash – Postcard</title>
<link href="https://fonts.googleapis.com/css2?family=Oswald:wght@400;500;700&family=Roboto:wght@400;500;700&display=swap" rel="stylesheet">
<style>
  :root{
    --red:#c8161d;
    --red-dark:#9e0f14;
    --charcoal:#2a2a2a;
    --ink:#333333;
    --paper:#ffffff;
    --panel:#eeeeee;
    --yellow:#f5c400;
    --stage:#e8e5e0;
    --stamp:#c9c9c9;
  }
  *{margin:0;padding:0;box-sizing:border-box}
  html,body{width:826px;height:1200px;overflow:hidden}
  body{background:var(--stage);position:relative;font-family:'Roboto',sans-serif;color:var(--ink)}
  .postcard{position:absolute;left:33px;width:760px;height:488px;background:var(--paper);overflow:hidden;box-shadow:0 6px 18px rgba(0,0,0,.25)}
  .postcard--front{top:70px}
  .postcard--back{top:640px}
  .shapes{position:absolute;inset:0}
  .abs{position:absolute}

  /* front */
  .front-tag{left:22px;top:38px;background:var(--charcoal);color:#fff;font-family:'Oswald',sans-serif;font-size:15px;letter-spacing:.5px;padding:3px 10px;text-transform:uppercase}
  .front-cash{left:20px;top:62px;font-family:'Oswald',sans-serif;font-weight:700;font-size:80px;line-height:1;color:var(--red);letter-spacing:1px}
  .front-rule{left:22px;top:156px;width:196px;height:3px;background:var(--red)}
  .front-conditions{left:24px;top:170px;list-style:none;font-size:22px;line-height:1.3;color:var(--ink)}
  .front-conditions li:first-child{color:var(--red)}
  .offer{left:468px;top:180px;width:270px;text-align:center;font-family:'Oswald',sans-serif;color:var(--charcoal)}
  .offer__lead{font-size:31px;font-weight:700;line-height:1.05}
  .offer__time{font-size:15px;color:var(--red);font-weight:500;letter-spacing:1px}
  .offer__now{font-size:60px;font-weight:700;line-height:1}
  .perks{left:28px;top:335px;list-style:none;color:#fff;font-size:22px;line-height:1.3}
  .perks li::before{content:"•";color:var(--yellow);margin-right:8px}
  .front-contact{left:470px;top:345px;color:#fff}
  .front-contact__phone{font-size:22px;font-weight:500}
  .front-contact__email{font-size:12px;margin-top:4px}
  .front-web{left:440px;top:426px;width:320px;height:36px;background:var(--charcoal);color:#fff;font-size:19px;padding:6px 0 0 36px}

  /* back */
  .back-title{left:0;top:0;width:760px;height:74px;background:var(--charcoal);font-family:'Oswald',sans-serif;font-weight:700;font-size:40px;color:#fff;padding:10px 0 0 28px;text-transform:uppercase;letter-spacing:.5px}
  .back-title .hl{color:var(--yellow)}
  .back-title .accent{color:var(--red)}
  .back-copy{left:20px;top:88px;width:295px;color:#fff;font-size:10.5px;line-height:1.4}
  .back-copy p+p{margin-top:5px}
  .agent-photo{left:20px;top:176px;width:78px;height:84px}
  .back-contact{left:112px;top:186px;color:#fff}
  .back-contact__phone{font-size:19px;font-weight:500}
  .back-contact__email{font-size:11px;margin-top:3px}
  .back-web{left:20px;top:278px;color:#fff;font-size:16px}
  .stamp{left:672px;top:96px;width:62px;height:62px;background:var(--stamp)}
</style>
</head>
<body>

<section class="postcard postcard--front" aria-label="Postcard front">
  <svg class="shapes" width="760" height="488" viewBox="0 0 760 488" aria-hidden="true">
    <rect x="0" y="0" width="760" height="310" fill="var(--panel)"/>
    <polygon points="0,300 760,300 760,488 0,488" fill="var(--red)"/>
    <polygon points="0,470 760,470 760,488 0,488" fill="var(--charcoal)"/>
    <polygon points="280,0 330,0 240,300 190,300" fill="var(--red)" opacity=".9"/>
  </svg>

  <svg class="abs" style="left:0;top:0" width="760" height="488" viewBox="0 0 760 488">
    <defs>
      <linearGradient id="houseA" x1="0" y1="0" x2="0" y2="1"><stop offset="0" stop-color="#8aa9c8"/><stop offset="1" stop-color="#b99a7a"/></linearGradient>
      <linearGradient id="houseB" x1="0" y1="0" x2="0" y2="1"><stop offset="0" stop-color="#a3bed6"/><stop offset="1" stop-color="#c7a985"/></linearGradient>
      <linearGradient id="signSky" x1="0" y1="0" x2="1" y2="1"><stop offset="0" stop-color="#7ea5cf"/><stop offset="1" stop-color="#d5dde6"/></linearGradient>
      <linearGradient id="handsHouse" x1="0" y1="0" x2="1" y2="1"><stop offset="0" stop-color="#d6c1a9"/><stop offset="1" stop-color="#8d7666"/></linearGradient>
    </defs>
    <polygon role="img" aria-label="Photo of a brick family house" points="292,22 460,22 440,110 272,110" fill="url(#houseA)" stroke="#fff" stroke-width="4"/>
    <polygon role="img" aria-label="Photo of a stucco house" points="268,122 420,122 402,200 250,200" fill="url(#houseB)" stroke="#fff" stroke-width="4"/>
    <polygon role="img" aria-label="Photo of a suburban house" points="244,212 400,212 382,290 226,290" fill="url(#houseA)" stroke="#fff" stroke-width="4"/>
    <polygon role="img" aria-label="Photo of a hand holding house keys by a for-sale sign" points="470,0 760,0 760,165 432,165" fill="url(#signSky)"/>
    <polygon role="img" aria-label="Photo of hands holding a small model house" points="252,326 430,326 408,446 230,446" fill="url(#handsHouse)" stroke="#fff" stroke-width="4"/>
  </svg>

  <div class="abs front-tag">Tovin buys houses on</div>
  <div class="abs front-cash">CASH</div>
  <div class="abs front-rule"></div>
  <ul class="abs front-conditions">
    <li>Any Problem</li>
    <li>Any situation</li>
    <li>Any condition</li>
  </ul>

  <div class="abs offer">
    <div class="offer__lead">GET A CASH</div>
    <div class="offer__time">WITHIN 24 HOURS</div>
    <div class="offer__now">NOW!</div>
  </div>

  <ul class="abs perks">
    <li>No costs</li>
    <li>quick cash</li>
    <li>Sell as is</li>
    <li>NO commison</li>
  </ul>

  <div class="abs front-contact">
    <div class="front-contact__phone">Call us at 347 815 9026</div>
    <div class="front-contact__email">Email us at : info@brelkaporch.com</div>
  </div>
  <div class="abs front-web">www.brelkaporch.com</div>
</section>

<section class="postcard postcard--back" aria-label="Postcard back">
  <svg class="shapes" width="760" height="488" viewBox="0 0 760 488">
    <defs>
      <linearGradient id="heroPhoto" x1="0" y1="0" x2="1" y2="1"><stop offset="0" stop-color="#b7cfe0"/><stop offset="1" stop-color="#9dbb86"/></linearGradient>
    </defs>
    <polygon points="0,74 340,74 340,320 0,320" fill="var(--red)"/>
    <polygon role="img" aria-label="Photo of a hand holding a model house" points="0,320 340,320 300,488 0,488" fill="url(#heroPhoto)"/>
    <polygon points="340,74 356,74 316,488 300,488" fill="var(--red-dark)"/>
    <polygon points="356,74 372,74 332,488 316,488" fill="#d7d7d7"/>
  </svg>

  <div class="abs back-title">Tovin <span class="hl">Buys Houses On</span> <span class="accent">Cash</span></div>

  <div class="abs back-copy">
    <p>We buy houses fast for cash in any condition. No repairs, no fees and no waiting on banks. Get a fair offer today and close on the date you choose.</p>
    <p>Behind on payments, facing foreclosure or a tough tenant? Call us now and we will make it simple.</p>
  </div>

  <svg class="abs agent-photo" width="78" height="84" viewBox="0 0 78 84">
    <rect role="img" aria-label="Portrait photo of the home buyer" x="0" y="0" width="78" height="84" fill="#cfd4d9" stroke="#fff" stroke-width="3"/>
  </svg>

  <div class="abs back-contact">
    <div class="back-contact__phone">Call us at 347 815 9026</div>
    <div class="back-contact__email">Email us at : info@brelkaporch.com</div>
  </div>
  <div class="abs back-web">www.brelkaporch.com</div>

  <div class="abs stamp" aria-label="Stamp area"></div>
</section>

</body>
</html>
```